Layout of a 14-page report

I need a professional, well-designed, layout for a 14-page free report I'm offering.
My colors are red/black/white and have a chalkboard theme in my header graphic which you can incorporate if you want: see my website here - http://lorabexter.example/. I am an SEO strategy consultant and this report is about "SEO Essentials."
The attachment contains a few images/designs and graphics I like that may help guide your creative process.
I would like to see the:
1. Cover page
2. inside spread layout of a standard page
3. inside spread layout of a "page with sidebar content" (indicated in the attachment)
The selected winner will complete all pages. Thank you!

```html
<!DOCTYPE html>
<html lang="en">
<head>
<meta charset="utf-8">
<title>SEO Essentials – Report Layout</title>
<link rel="stylesheet" href="https://fonts.googleapis.com/css2?family=Dosis:wght@300;400;700&family=Satisfy&display=swap">
<style>
  :root {
    --backdrop: #e8e5e1;
    --paper-edge: #f4f3f1;
    --chalk-dark: #2f2f2f;
    --chalk-mid: #4a4a4a;
    --chalk-light: #5c5c5c;
    --red: #c8161d;
    --red-glow: #e0343a;
    --disc: #3a3a3a;
    --chalk-white: #f2f2f2;
    --chalk-soft: #d9d9d9;
  }
  * { margin: 0; padding: 0; box-sizing: border-box; }
  html, body { width: 969px; height: 1200px; overflow: hidden; }
  body {
    background: var(--backdrop);
    position: relative;
    font-family: "Dosis", sans-serif;
  }
  .page {
    position: absolute;
    display: block;
    border: 5px solid var(--paper-edge);
    box-shadow: 0 3px 10px rgba(0,0,0,.25);
    background: var(--chalk-dark);
  }
  .page--cover-large { left: 150px; top: 90px; width: 669px; height: 470px; }
  .page--cover      { left: 132px; top: 640px; width: 342px; height: 242px; }
  .page--contents   { left: 494px; top: 640px; width: 342px; height: 242px; }
  .page--intro      { left: 132px; top: 910px; width: 342px; height: 242px; }
  .page--body       { left: 494px; top: 910px; width: 342px; height: 242px; }
  .page svg { width: 100%; height: 100%; display: block; }
  .kicker { font-family: "Dosis", sans-serif; fill: var(--chalk-white); }
  .script { font-family: "Satisfy", cursive; fill: var(--chalk-white); }
  .year { font-family: "Dosis", sans-serif; font-weight: 700; fill: var(--chalk-white); }
  .badge-label { font-family: "Dosis", sans-serif; font-weight: 700; fill: var(--chalk-soft); }
  .heading { font-family: "Dosis", sans-serif; fill: var(--chalk-white); }
  .toc { font-family: "Dosis", sans-serif; font-weight: 700; fill: var(--chalk-soft); font-size: 5.2px; }
  .toc-sub { font-family: "Dosis", sans-serif; font-weight: 400; fill: var(--chalk-soft); font-size: 5.2px; }
  .body-copy { font-family: "Dosis", sans-serif; fill: var(--chalk-soft); font-size: 4.3px; }
  .body-copy .lead { font-weight: 700; }
  .folio { font-family: "Dosis", sans-serif; fill: var(--chalk-soft); font-size: 7px; }
</style>
</head>
<body>

<!-- Cover, large -->
<div class="page page--cover-large">
  <svg viewBox="0 0 427 300" preserveAspectRatio="none">
    <defs>
      <radialGradient id="chalkboard" cx="40%" cy="40%" r="75%">
        <stop offset="0" stop-color="#5a5a5a"/>
        <stop offset=".6" stop-color="#414141"/>
        <stop offset="1" stop-color="#2b2b2b"/>
      </radialGradient>
      <radialGradient id="red-band" cx="75%" cy="70%" r="70%">
        <stop offset="0" stop-color="#e2363c"/>
        <stop offset="1" stop-color="#b5131a"/>
      </radialGradient>
      <radialGradient id="disc" cx="50%" cy="45%" r="60%">
        <stop offset="0" stop-color="#4e4e4e"/>
        <stop offset="1" stop-color="#2e2e2e"/>
      </radialGradient>
      <g id="cover-art">
        <rect width="427" height="300" fill="url(#chalkboard)"/>
        <path d="M405,0 C398,110 300,215 0,240 L0,300 L427,300 L427,0 Z" fill="url(#red-band)"/>
        <g fill="url(#disc)">
          <circle cx="50" cy="244" r="20"/>
          <circle cx="100" cy="288" r="22"/>
          <circle cx="185" cy="257" r="27"/>
          <circle cx="265" cy="257" r="21"/>
          <circle cx="350" cy="226" r="47"/>
          <circle cx="258" cy="180" r="21"/>
          <circle cx="350" cy="127" r="25"/>
          <circle cx="397" cy="162" r="14"/>
          <circle cx="400" cy="93" r="14"/>
        </g>
        <text class="badge-label" x="100" y="294" font-size="18" text-anchor="middle">@</text>
        <text class="badge-label" x="350" y="224" font-size="17" text-anchor="middle">SEO</text>
        <text class="badge-label" x="350" y="238" font-size="8" text-anchor="middle">Essentials</text>
        <text class="kicker" x="52" y="62" font-size="13.5"><tspan font-weight="700">WHERE IS</tspan> <tspan font-weight="300">DIGITAL</tspan></text>
        <text class="script" x="50" y="128" font-size="50">Marking</text>
        <text class="kicker" x="52" y="152" font-size="12" font-weight="300">HEADED IN</text>
        <text class="year" x="122" y="158" font-size="24">2015</text>
      </g>
    </defs>
    <use href="#cover-art"/>
  </svg>
</div>

<!-- Cover -->
<div class="page page--cover">
  <svg viewBox="0 0 427 300" preserveAspectRatio="none"><use href="#cover-art"/></svg>
</div>

<!-- Table of contents -->
<div class="page page--contents">
  <svg viewBox="0 0 427 300" preserveAspectRatio="none">
    <rect width="427" height="300" fill="url(#chalkboard)"/>
    <path d="M427,205 C400,250 330,285 250,300 L427,300 Z" fill="url(#red-band)"/>
    <circle cx="357" cy="248" r="27" fill="url(#disc)"/>
    <text class="heading" x="52" y="62" font-size="20"><tspan font-weight="300">TABLE OF</tspan> <tspan font-weight="700">CONTENTS</tspan></text>
    <g>
      <text class="toc" x="106" y="96">•</text><text class="toc" x="112" y="96">Introduction: A Checklist of SEO Essentials</text>
      <text class="toc-sub" x="120" y="110">◆</text><text class="toc-sub" x="130" y="110">1. Explore Motivations, Determine KPIs, Manage Expectations</text>
      <text class="toc-sub" x="120" y="124">◆</text><text class="toc-sub" x="130" y="124">2. “Would You Give This Site Your Credit Card?”</text>
      <text class="toc-sub" x="120" y="138">◆</text><text class="toc-sub" x="130" y="138">3. Website Marketing Fundamentals: Engagement</text>
      <text class="toc-sub" x="120" y="152">◆</text><text class="toc-sub" x="130" y="152">4. SEO’s Foundational Individual Elements</text>
      <text class="toc-sub" x="120" y="166">◆</text><text class="toc-sub" x="130" y="166">5. Take a Holistic View: Benchmark Individual Elements and Then the Site as a Whole</text>
      <text class="toc-sub" x="120" y="180">◆</text><text class="toc-sub" x="130" y="180">6. Getting Lead Gen Results</text>
      <text class="toc-sub" x="120" y="194">◆</text><text class="toc-sub" x="130" y="194">7. Foundational SEO: Your First Order of Business</text>
      <text class="toc-sub" x="120" y="208">◆</text><text class="toc-sub" x="130" y="208">8. Integrate Ongoing SEO into Marketing Routine</text>
      <text class="toc" x="106" y="222">•</text><text class="toc" x="112" y="222">Summary</text>
      <text class="toc" x="106" y="236">•</text><text class="toc" x="112" y="236">About Lora</text>
      <text class="toc" x="106" y="250">•</text><text class="toc" x="112" y="250">Resource Links</text>
    </g>
    <text class="folio" x="357" y="251" text-anchor="middle">01</text>
  </svg>
</div>

<!-- Introduction page -->
<div class="page page--intro">
  <svg viewBox="0 0 427 300" preserveAspectRatio="none">
    <rect width="427" height="300" fill="url(#chalkboard)"/>
    <path d="M0,200 C40,250 120,285 240,300 L0,300 Z" fill="url(#red-band)"/>
    <circle cx="64" cy="248" r="27" fill="url(#disc)"/>
    <text class="heading" x="52" y="62" font-size="11"><tspan font-weight="700">INTRODUCTION:</tspan> <tspan font-weight="300">A CHECKLIST OF SEO ESSENTIALS</tspan></text>
    <text class="body-copy">
      <tspan x="93" y="92">For my clients and the marketers I am acquainted with, time is their most precious resource.</tspan>
      <tspan x="93" y="104">They have to guard their time like a bulldog. And within this limited time, they have the fun challenge of being</tspan>
      <tspan x="93" y="116">expected to consistently produce more and better results. And the really good marketers, well, they don’t solely</tspan>
      <tspan x="93" y="128">want results. They want to make a contribution, become better at their craft, and genuinely help their organiza-</tspan>
      <tspan x="93" y="140">tion grow by driving more traffic, awareness, and of course leads.</tspan>
      <tspan x="93" y="152">The beauty of search engine optimization (SEO) is it helps with all of the above: efficiency, results, contribution,</tspan>
      <tspan x="93" y="164">growth and leads.</tspan>
      <tspan x="93" y="176">But when it comes to effectively deploying SEO and hitting KPIs and objectives, marketers are often held back by</tspan>
      <tspan x="93" y="188">a lack of time, resources, and knowledge about where to even begin.</tspan>
      <tspan x="93" y="200" class="lead">SEO: Simple, But Not Easy</tspan>
      <tspan x="93" y="212">I personally dislike the phrase, “simple but not easy.” A statement like that needs to be backed up with a more</tspan>
      <tspan x="93" y="224">detailed explanation, don’t you think? It makes my brain hurt to think about the implications and makes me</tspan>
      <tspan x="93" y="236">wish someone would just spell out what is not so easy so I know what I’m getting into. That being said…</tspan>
    </text>
    <text class="folio" x="64" y="251" text-anchor="middle">02</text>
  </svg>
</div>

<!-- Standard body page -->
<div class="page page--body">
  <svg viewBox="0 0 427 300" preserveAspectRatio="none">
    <rect width="427" height="300" fill="url(#chalkboard)"/>
    <path d="M427,195 C395,250 320,285 230,300 L427,300 Z" fill="url(#red-band)"/>
    <circle cx="357" cy="248" r="27" fill="url(#disc)"/>
    <text class="body-copy">
      <tspan x="95" y="56" class="lead">…SEO is simple but not easy.</tspan>
      <tspan x="95" y="68">I truly believe that SEO is simpler than ever, but not easy, due to the multiple disciplines and activities that have</tspan>
      <tspan x="95" y="80">to come together in order to realize long term, sustainable success.</tspan>
      <tspan x="95" y="92">SEO success today requires a mix of best practices, trends, marketing 101, and SEO fundamentals meshed</tspan>
      <tspan x="95" y="104">together.</tspan>
      <tspan x="95" y="116">But believe me, the headache is worth it. If you…</tspan>
      <tspan x="95" y="128">•</tspan><tspan x="112" y="128">know you’re missing opportunities</tspan>
      <tspan x="95" y="140">•</tspan><tspan x="112" y="140">want to attract a certain type of customer but aren’t sure how</tspan>
      <tspan x="95" y="152">•</tspan><tspan x="112" y="152">are overly dependent on pricey paid marketing services like PPC at the expense of organic SEO or other</tspan>
      <tspan x="112" y="164">lower-cost alternatives</tspan>
      <tspan x="95" y="176">•</tspan><tspan x="112" y="176">have tried SEO but got busy and you know the stop-and-go efforts won’t produce results you know are</tspan>
      <tspan x="112" y="188">attainable</tspan>
      <tspan x="95" y="200">…then this guide is for you. In this 8-point checklist I’ll explain the essential elements of SEO and how to gener-</tspan>
      <tspan x="95" y="212">ate more leads to your site consistently.</tspan>
      <tspan x="95" y="224">All it takes is a solid start, a plan for consistent action, and time and momentum in the right direction.</tspan>
    </text>
    <text class="folio" x="357" y="251" text-anchor="middle">03</text>
  </svg>
</div>

</body>
</html>
```